Brookvane Consulting Business Card Design

Business Card Design for Brookvane Consulting. Brookvane Consulting is a boutique consultancy based in Atlanta, GA., that specializes in marketing strategy, organization planning, and leadership development. We provide solutions for small businesses and startups as well as Vantage 300 companies.

http://brookvaneconsulting.com/

Target Market(s)

We provide solutions for small businesses and startups as well as Vantage 300 companies.

Industry/Entity Type

Consulting

Contact Information for Business Card

Two sided business card with priority on contact information, logo, tag line (Clear Thinking to Plan Well, Act Well, Grow Well)

Colors

Designer to choose colors to be used in the design.

Requirements
Must have
• contact information, logo, tag line (Clear Thinking to Plan Well, Act Well, Grow Well)
• Simple no over communication.
Nice to have
• I would like to see different placements of logo and creative use of both sides of the card
Should not have
• Do not put too much information on the card.

```html
<!DOCTYPE html>
<html lang="en">
<head>
<meta charset="utf-8">
<title>Brookvane Consulting – Business Card</title>
<link href="https://fonts.googleapis.com/css2?family=Lato:wght@400;700&display=swap" rel="stylesheet">
<style>
  :root {
    --backdrop: #2f2926;
    --card-black: #161616;
    --ink: #111111;
    --paper: #ffffff;
    --band-grey: #b9b9b9;
    --muted: #a3a3a3;
    --tagline: #e6e6e6;
  }
  * { box-sizing: border-box; margin: 0; padding: 0; }
  html, body {
    width: 1200px; height: 769px; overflow: hidden;
    background: var(--backdrop);
    font-family: "Lato", Arial, sans-serif;
  }
  .stage {
    position: relative; width: 1200px; height: 769px;
    display: flex; align-items: center; justify-content: center; gap: 50px;
  }
  .card {
    position: relative; width: 530px; height: 303px;
    border-radius: 3px; overflow: hidden;
    box-shadow: 0 10px 30px rgba(0,0,0,.45);
  }

  /* Front side */
  .card--front { background: var(--paper); }
  .front__header {
    position: absolute; left: 0; top: 0; width: 100%; height: 118px;
    background: var(--card-black);
  }
  .brand {
    display: flex; align-items: center; gap: 10px;
    color: var(--paper); font-weight: 700; letter-spacing: .5px;
    white-space: nowrap;
  }
  .brand__mark { width: 12px; height: 12px; background: var(--paper); flex: none; }
  .front__header .brand { position: absolute; left: 38px; top: 44px; font-size: 26px; }
  .front__band {
    position: absolute; left: 0; top: 118px; width: 100%; height: 74px;
    background: linear-gradient(to right, var(--paper) 0 70%, var(--band-grey) 70% 100%);
  }
  .front__art {
    position: absolute; right: 0; top: 118px; width: 160px; height: 100px;
    background: linear-gradient(135deg, #d8d8d8 0%, #7a7a7a 100%);
  }
  .contact {
    position: absolute; left: 38px; top: 168px; color: var(--ink);
  }
  .contact__name { font-size: 17px; font-weight: 700; letter-spacing: .3px; line-height: 20px; }
  .contact__role { font-size: 13px; color: var(--muted); margin-bottom: 8px; line-height: 17px; }
  .contact__list { list-style: none; font-size: 13px; line-height: 19px; }
  .contact__list li { display: flex; align-items: center; gap: 8px; }
  .contact__list svg { width: 11px; height: 11px; fill: var(--ink); flex: none; }

  /* Back side */
  .card--back {
    background: var(--card-black);
    display: flex; flex-direction: column; align-items: center; justify-content: center;
  }
  .card--back .brand { font-size: 34px; }
  .tagline {
    margin-top: 34px; color: var(--tagline); font-size: 12px; letter-spacing: .3px;
  }
</style>
</head>
<body>
<main class="stage">
  <section class="card card--front" aria-label="Front of business card">
    <div class="front__header">
      <div class="brand"><span class="brand__mark"></span>Brookvane Consulting</div>
    </div>
    <div class="front__band"></div>
    <div class="front__art" role="img" aria-label="Large pencil tip illustration in black and grey"></div>
    <div class="contact">
      <p class="contact__name">DORIAN WHITFIELD</p>
      <p class="contact__role">Founder/Managing Director</p>
      <ul class="contact__list">
        <li><svg viewBox="0 0 16 16"><path d="M3 1l3 0 1.5 4-2 1.3a9 9 0 0 0 4.2 4.2L11 8.5l4 1.5v3a2 2 0 0 1-2 2C6.9 15 1 9.1 1 3a2 2 0 0 1 2-2z"/></svg>404-555-0187</li>
        <li><svg viewBox="0 0 16 16"><path d="M1 3h14v10H1z M1 3l7 6 7-6" fill="none" stroke="#111" stroke-width="1.6"/></svg>dorian@brookvaneconsulting.com</li>
        <li><svg viewBox="0 0 16 16"><circle cx="8" cy="8" r="7"/></svg>brookvaneconsulting.com</li>
      </ul>
    </div>
  </section>

  <section class="card card--back" aria-label="Back of business card">
    <div class="brand"><span class="brand__mark"></span>Brookvane Consulting</div>
    <p class="tagline">Clear Thinking to Plan Well, Act Well, Grow Well</p>
  </section>
</main>
</body>
</html>
```